Mobile Fitness snd Therapy Business Card Design

I need a business card designed for my mobile fitness and therapy business.

Please view the images that I have uploaded. I like the simplicity of the design that I have attached. I adapted it with my information

Target Market(s)

Those seeking personal training, injury rehabilitation or massage therapy.

Industry/Entity Type

Business

Contact Information for Business Card

Derek Fulham - MSc, CAT(C), RMT, CSCS, Pn2
e-mail: derek@vantrelo.com
website: www.vantrelo.com
instagram: @derek_fulham

Font styles to use
Sans Serif

Colors
3176b5
0355a3

Requirements
Must have
• "Contact us to receive a FREE assessment"
• Services offered:
• Personal Training
• Golf Fitness
• Injury Rehab
• Massage Therapy
• Yoga
Nice to have
• Consistent colours with brand
• - Dark Blue: #232837
• - Blue: #5096f0
• Consistent look/feel with the website: www.vantrelo.com

```html
<!DOCTYPE html>
<html lang="en">
<head>
<meta charset="utf-8">
<title>Vantrelo Business Card</title>
<link href="https://fonts.googleapis.com/css2?family=Open+Sans:wght@400;600;700&display=swap" rel="stylesheet">
<style>
  :root {
    --backdrop: #3b3531;
    --card: #0c0c0d;
    --card-edge: #1a1a1c;
    --text: #ffffff;
    --text-soft: #e6e6e6;
    --rule: #6a6a6e;
    --brand-blue: #3176b5;
    --name-blue: #2f6fd6;
    --icon-blue: #5096f0;
  }
  * { box-sizing: border-box; margin: 0; padding: 0; }
  html, body {
    width: 1200px; height: 844px; overflow: hidden;
    background: var(--backdrop);
    font-family: "Open Sans", Arial, sans-serif;
  }
  .stage {
    position: relative; width: 1200px; height: 844px;
    display: flex; align-items: center; justify-content: center; gap: 40px;
  }
  .card {
    position: relative; width: 540px; height: 309px;
    background: var(--card);
    border: 1px solid var(--card-edge);
    color: var(--text);
  }
  .wordmark {
    font-weight: 700; color: var(--text);
    letter-spacing: 4px; line-height: 1;
    display: flex; align-items: center; gap: 12px;
  }
  .wordmark-square {
    width: 14px; height: 14px; background: var(--brand-blue);
  }
  .rule { position: absolute; height: 1px; background: var(--rule); }

  /* Front */
  .card-front .wordmark { position: absolute; left: 40px; top: 78px; font-size: 40px; }
  .card-front .rule-top { left: 40px; right: 40px; top: 138px; }
  .contact-list {
    position: absolute; right: 40px; top: 152px;
    list-style: none; text-align: right; font-size: 13.5px; line-height: 19px;
    color: var(--text-soft);
  }
  .contact-list li { display: flex; justify-content: flex-end; align-items: center; gap: 6px; }
  .contact-list svg { width: 11px; height: 11px; }
  .card-front .rule-bottom { left: 40px; right: 40px; top: 232px; }
  .holder { position: absolute; left: 40px; top: 244px; }
  .holder-name { font-size: 21px; font-weight: 600; color: var(--name-blue); line-height: 1.15; }
  .holder-credentials { font-size: 13px; color: var(--text-soft); margin-top: 2px; }

  /* Back */
  .card-back { text-align: center; }
  .card-back .wordmark { justify-content: center; margin-top: 46px; font-size: 44px; }
  .card-back .rule-top { left: 50px; right: 50px; top: 110px; }
  .offer { position: absolute; left: 0; right: 0; top: 120px; font-size: 17px; }
  .card-back .rule-bottom { left: 50px; right: 50px; top: 154px; }
  .services-title {
    position: absolute; left: 0; right: 0; top: 166px;
    font-size: 22px; font-weight: 700; text-decoration: underline; text-underline-offset: 3px;
  }
  .services-list {
    position: absolute; left: 0; right: 0; top: 206px;
    font-size: 20px; line-height: 29px;
  }
</style>
</head>
<body>
<main class="stage">
  <section class="card card-front" aria-label="Card front">
    <div class="wordmark">VANTRELO<span class="wordmark-square"></span></div>
    <div class="rule rule-top"></div>
    <ul class="contact-list">
      <li>derek@vantrelo.com
        <svg viewBox="0 0 12 12"><rect x="0.5" y="2" width="11" height="8" fill="var(--icon-blue)"/><path d="M0.5 2 L6 7 L11.5 2" stroke="var(--card)" fill="none"/></svg>
      </li>
      <li>www.vantrelo.com
        <svg viewBox="0 0 12 12"><circle cx="6" cy="6" r="5.5" fill="var(--icon-blue)"/><path d="M0.5 6h11M6 0.5c-3 3-3 8 0 11M6 0.5c3 3 3 8 0 11" stroke="var(--card)" stroke-width="0.8" fill="none"/></svg>
      </li>
      <li>@derek_fulham
        <svg viewBox="0 0 12 12"><circle cx="6" cy="6" r="5.5" fill="var(--icon-blue)"/></svg>
      </li>
    </ul>
    <div class="rule rule-bottom"></div>
    <div class="holder">
      <p class="holder-name">DEREK FULHAM</p>
      <p class="holder-credentials">MSc, CAT(C), RMT, CSCS, Pn2</p>
    </div>
  </section>

  <section class="card card-back" aria-label="Card back">
    <div class="wordmark">VANTRELO<span class="wordmark-square"></span></div>
    <div class="rule rule-top"></div>
    <p class="offer">Contact us to receive a FREE assessment</p>
    <div class="rule rule-bottom"></div>
    <h2 class="services-title">SERVICES OFFERED</h2>
    <p class="services-list">Personal Training - Golf Fitness<br>Injury Rehab - Massage Therapy - Yoga</p>
  </section>
</main>
</body>
</html>
```